Business Cards

Need business card design that I can update for new employees and details. Needs to incorporate our logo, be bright and fun (in line with tourism and holidays)
Would like a Map of Western Australia on the front with locations all the caravan parks we own (just purchased Tom Price so please include that as well as others listed on our website).
Target Market(s)
Famillies
Contact Information for Business Card
5 Cards -
Neil Perrow (Director) e: perrow@wattlebay.com.au p: 0491 570 156
Mira Perrow (Director) e: perrow@wattlebay.com.au p: 0491 570 157
Owen Halvey (General Manager) e: halvey@wattlebay.com.au p: 0491 570 158
Helen Halvey (General Manager) e: halvey@wattlebay.com.au p: 0491 570 159
Colin Danby (Training and Operations Manager) - e: danby@wattlebay.com.au p:0491 570 110
Colors
Look and feel

```html
<!DOCTYPE html>
<html lang="en">
<head>
<meta charset="utf-8">
<title>Wattlebay Tourist Parks – Business Cards</title>
<link rel="stylesheet" href="https://fonts.googleapis.com/css2?family=Roboto+Condensed:wght@300;400;700&display=swap">
<style>
  :root {
    --backdrop: #e7e4df;
    --paper: #fbfbfb;
    --cyan: #45bccb;
    --cyan-light: #6ccfda;
    --sea-green: #6fbfae;
    --sea-green-dark: #5aae9d;
    --ink-grey: #6d6f72;
    --card-black: #1c1d1f;
    --white: #ffffff;
  }
  * { margin: 0; padding: 0; box-sizing: border-box; }
  html, body { width: 1200px; height: 911px; overflow: hidden; }
  body {
    background: var(--backdrop);
    font-family: "Roboto Condensed", Arial, sans-serif;
    position: relative;
  }
  .card {
    position: absolute;
    width: 640px;
    height: 390px;
    box-shadow: 0 10px 30px rgba(0,0,0,0.25);
    overflow: hidden;
  }
  /* Front card */
  .card-front { left: 60px; top: 50px; background: var(--paper); }
  .front-brand {
    position: absolute; left: 0; top: 0; width: 300px; height: 390px;
    display: flex; align-items: center; justify-content: center; gap: 12px;
  }
  .brand-square {
    width: 26px; height: 26px; background: var(--cyan); flex: none;
  }
  .brand-name {
    color: var(--ink-grey); font-weight: 300; font-size: 24px;
    letter-spacing: 2px; text-transform: uppercase; line-height: 1.15;
  }
  .front-panel { position: absolute; left: 300px; top: 0; width: 340px; height: 390px; }
  .front-panel svg { position: absolute; inset: 0; }
  .holder {
    position: absolute; right: 26px; top: 26px; text-align: right; color: var(--white);
  }
  .holder-name { font-weight: 700; font-size: 24px; text-transform: uppercase; letter-spacing: 0.5px; }
  .holder-role { font-weight: 400; font-size: 15px; text-transform: uppercase; letter-spacing: 1px; margin-top: 2px; }
  .contacts {
    position: absolute; right: 26px; bottom: 26px; list-style: none; color: var(--white);
    font-weight: 300; font-size: 16px;
  }
  .contacts li { display: flex; align-items: center; justify-content: flex-end; gap: 8px; margin-top: 5px; }
  .contacts svg { width: 13px; height: 13px; flex: none; }
  /* Back card */
  .card-back { left: 500px; top: 470px; background: var(--card-black); }
  .back-web {
    position: absolute; left: 34px; top: 50%;
    transform: translate(-50%, -50%) rotate(90deg) translateY(-0px);
    transform-origin: center;
    color: var(--white); font-size: 15px; letter-spacing: 3.5px; font-weight: 300;
    white-space: nowrap; margin-left: 10px;
  }
  .back-brand {
    position: absolute; inset: 0; display: flex; align-items: center; justify-content: center; gap: 14px;
  }
  .back-brand .brand-name { color: var(--cyan-light); font-size: 26px; }
</style>
</head>
<body>
  <section class="card card-front" aria-label="Business card front">
    <div class="front-brand">
      <span class="brand-square"></span>
      <span class="brand-name">Wattlebay<br>Tourist Parks</span>
    </div>
    <div class="front-panel">
      <svg viewBox="0 0 340 390" preserveAspectRatio="none" aria-hidden="true">
        <rect width="340" height="390" fill="var(--sea-green)"/>
        <path d="M0 0 H340 V180 C250 185 200 70 120 100 C70 118 40 125 0 125 Z" fill="var(--cyan)"/>
        <path d="M0 125 C40 125 70 118 120 100 C200 70 250 185 340 180" fill="none" stroke="var(--white)" stroke-width="9"/>
      </svg>
      <div class="holder">
        <div class="holder-name">Neil Perrow</div>
        <div class="holder-role">Director</div>
      </div>
      <ul class="contacts">
        <li>0491 570 156
          <svg viewBox="0 0 16 16"><path d="M4 1 L6.5 4.5 L5 6.5 C6 8.5 7.5 10 9.5 11 L11.5 9.5 L15 12 L13 15 C6.5 14 2 9.5 1 3 Z" fill="var(--white)"/></svg></li>
        <li>perrow@wattlebay.com.au
          <svg viewBox="0 0 16 16"><rect x="1" y="3" width="14" height="10" fill="var(--white)"/><path d="M1 3 L8 9 L15 3" fill="none" stroke="var(--sea-green)" stroke-width="1.4"/></svg></li>
        <li>www.wattlebay.com.au
          <svg viewBox="0 0 16 16"><circle cx="8" cy="8" r="7" fill="var(--white)"/><path d="M1 8 H15 M8 1 C4 5 4 11 8 15 M8 1 C12 5 12 11 8 15" fill="none" stroke="var(--sea-green)" stroke-width="1.1"/></svg></li>
      </ul>
    </div>
  </section>

  <section class="card card-back" aria-label="Business card back">
    <div class="back-web">www.wattlebay.com.au</div>
    <div class="back-brand">
      <span class="brand-square"></span>
      <span class="brand-name">Wattlebay<br>Tourist Parks</span>
    </div>
  </section>
</body>
</html>
```